Dunmore Roofing

Want a professional looking business card

Industry/Entity Type

Business

Contact Information for Business Card

Paul Dunmore ( Owner) paul@dunmoreroofing-example.com, www.dunmoreroofing-example.com, Adress: 4172 Township road 43 Harlowfield,ON K9X4T2

```html
<!DOCTYPE html>
<html lang="en">
<head>
<meta charset="utf-8">
<title>Dunmore Roofing – Business Card</title>
<link rel="stylesheet" href="https://fonts.googleapis.com/css2?family=Ubuntu:wght@500;700&family=Open+Sans:wght@400;600;700&display=swap">
<style>
  :root {
    --backdrop: #e9e7e4;
    --brand-blue: #1c4585;
    --brand-grey: #7b7c7e;
    --card-white: #ffffff;
    --text-light: #ffffff;
    --text-soft: #e3e9f3;
  }
  * { margin: 0; padding: 0; box-sizing: border-box; }
  html, body { width: 1200px; height: 900px; overflow: hidden; }
  body { background: var(--backdrop); position: relative; font-family: "Open Sans", sans-serif; }

  .card { position: absolute; box-shadow: 0 6px 18px rgba(0,0,0,.18); }

  /* Front of card */
  .card-front { left: 182px; top: 84px; width: 588px; height: 364px; background: var(--brand-blue); display: flex; }
  .brand-strip { width: 152px; height: 100%; background: var(--brand-grey); position: relative; display: flex; align-items: center; justify-content: center; }
  .brand-strip-name { transform: rotate(-90deg); white-space: nowrap; font-family: "Ubuntu", sans-serif; font-weight: 700; font-size: 26px; letter-spacing: 2px; color: var(--text-light); text-transform: uppercase; }

  .contact { padding: 86px 0 0 48px; color: var(--text-light); }
  .contact-name { font-family: "Ubuntu", sans-serif; font-weight: 700; font-size: 23px; letter-spacing: .3px; line-height: 1; text-transform: uppercase; }
  .contact-role { font-size: 15px; color: var(--text-soft); margin-top: 2px; }
  .contact-list { list-style: none; margin-top: 32px; font-size: 15px; line-height: 21px; }
  .contact-list li { display: flex; align-items: flex-start; gap: 7px; }
  .contact-list .address { margin-top: 24px; }
  .contact-list svg { flex: none; margin-top: 5px; fill: var(--text-light); }

  /* Back of card */
  .card-back { left: 430px; top: 492px; width: 566px; height: 350px; background: var(--card-white); text-align: center; }
  .back-brand { position: absolute; left: 0; right: 0; top: 178px; display: flex; align-items: center; justify-content: center; gap: 14px; }
  .back-brand-mark { width: 22px; height: 22px; background: var(--brand-blue); }
  .back-brand-name { font-family: "Ubuntu", sans-serif; font-weight: 700; font-size: 40px; letter-spacing: 2px; color: var(--brand-blue); text-transform: uppercase; }
  .back-web { position: absolute; left: 0; right: 0; top: 282px; font-weight: 700; font-size: 15px; color: var(--brand-blue); }
</style>
</head>
<body>

<section class="card card-front" aria-label="Business card front">
  <div class="brand-strip">
    <span class="brand-strip-name">Dunmore Roofing</span>
  </div>
  <div class="contact">
    <h1 class="contact-name">Paul Dunmore</h1>
    <p class="contact-role">Owner</p>
    <ul class="contact-list">
      <li>
        <svg width="13" height="10" viewBox="0 0 13 10" aria-hidden="true"><path d="M0 0h13v10H0z M1 1.2v.6l5.5 3.6L12 1.8v-.6L6.5 4.6z" fill-rule="evenodd"/></svg>
        <span>paul@dunmoreroofing-example.com</span>
      </li>
      <li>
        <svg width="13" height="13" viewBox="0 0 13 13" aria-hidden="true"><circle cx="6.5" cy="6.5" r="6.5"/><path d="M1 6.5h11M6.5 1c2.2 2.5 2.2 8.5 0 11M6.5 1c-2.2 2.5-2.2 8.5 0 11" stroke="#1c4585" stroke-width="1" fill="none"/></svg>
        <span>www.dunmoreroofing-example.com</span>
      </li>
      <li class="address">
        <svg width="12" height="16" viewBox="0 0 12 16" aria-hidden="true"><path d="M6 0a6 6 0 0 1 6 6c0 4-6 10-6 10S0 10 0 6a6 6 0 0 1 6-6zm0 3.5a2.5 2.5 0 1 0 0 5 2.5 2.5 0 0 0 0-5z" fill-rule="evenodd"/></svg>
        <span>4172 Township road 43<br>Harlowfield,ON K9X4T2</span>
      </li>
    </ul>
  </div>
</section>

<section class="card card-back" aria-label="Business card back">
  <div class="back-brand">
    <span class="back-brand-mark"></span>
    <span class="back-brand-name">Dunmore Roofing</span>
  </div>
  <p class="back-web">www.dunmoreroofing-example.com</p>
</section>

</body>
</html>
```